TL - business card

Tallow Partners is an insurance brokerage firm, inovative, proactive, vigorous, which aims to become the leader of the insurance brokers in Anfrica. We should like to get some designs which should be avoided also in Gray / Metallic for the Administration and Orange / Blue for the Managers (ike in the picture sent). The Blue / Green logo is not the correct one, but the source of the file. Please adjust the color accordingly for the business cards. 1 / Orange / Blue 2 / Gray / Metallic We want something classic but which is transmitted strenght, inovation, modernity and most of all, rapidity. We want something start-up like, very punchy and catching eye remaining profesional at the same time. Name: Dorian Whitlock Function: Managing Director Address: N ° 17/18 Rua Veloso - R / C 2B Direita - Bairro Mutamba - Luanda Tel: (+244) 947 582 316 Email: dorian.whitlock@tallow-p.example Website: www.tallow-p. example We want classic in the front and creative, colorfull at the back. The cards will be printed in relief, with very high quality of paper.
Insurance Broker
Colors
Designer to choose colors to be used in the design.

```html
<!DOCTYPE html>
<html lang="en">
<head>
<meta charset="utf-8">
<title>Tallow Partners – Business Card</title>
<link rel="stylesheet" href="https://fonts.googleapis.com/css2?family=Exo+2:wght@500;700&family=Lato:wght@400&display=swap">
<style>
  :root {
    --backdrop: #3b3b3b;
    --card-white: #ffffff;
    --brand-orange: #ec6723;
    --brand-blue: #29a8e0;
    --ink: #2b2b2b;
    --radius-big: 56px;
  }
  * { margin: 0; padding: 0; box-sizing: border-box; }
  html, body { width: 1200px; height: 900px; overflow: hidden; }
  body {
    background: var(--backdrop);
    position: relative;
    font-family: "Lato", sans-serif;
    color: var(--ink);
  }
  .card {
    position: absolute;
    top: 200px;
    width: 310px;
    height: 502px;
    box-shadow: 3px 4px 6px rgba(0,0,0,0.45);
  }
  .card-front {
    left: 253px;
    background: var(--card-white);
    border-radius: var(--radius-big) 0 var(--radius-big) 0;
  }
  .card-back {
    left: 627px;
    width: 309px;
    border-radius: 0 var(--radius-big) 0 var(--radius-big);
    background: linear-gradient(200deg, var(--brand-blue) 8%, #8a8f93 48%, var(--brand-orange) 92%);
  }
  .brand {
    position: absolute;
    left: 0; right: 0;
    top: 90px;
    text-align: center;
  }
  .brand-dot {
    display: block;
    width: 78px; height: 78px;
    margin: 0 auto 14px;
    border: 6px solid var(--brand-orange);
    border-radius: 50%;
  }
  .brand-name {
    font-family: "Exo 2", sans-serif;
    font-weight: 700;
    font-size: 23px;
    letter-spacing: 0.5px;
    color: var(--brand-orange);
    text-transform: uppercase;
  }
  .contact {
    position: absolute;
    left: 33px;
    top: 315px;
  }
  .person-name {
    font-family: "Exo 2", sans-serif;
    font-weight: 500;
    font-size: 18px;
    letter-spacing: 0.3px;
    text-transform: uppercase;
    line-height: 22px;
  }
  .person-name .first { color: var(--brand-orange); }
  .person-name .last { color: var(--brand-blue); }
  .role { font-size: 14px; line-height: 18px; margin-bottom: 10px; }
  .line { font-size: 14px; line-height: 19px; display: flex; align-items: center; gap: 4px; }
  .line svg { width: 14px; height: 12px; flex: none; }
  .address { margin-top: 10px; font-size: 14px; line-height: 18px; }
  .back-mark {
    position: absolute;
    left: 0; right: 0;
    top: 178px;
    text-align: center;
  }
  .back-mark .brand-dot { width: 120px; height: 120px; border: 8px solid var(--card-white); margin-bottom: 0; }
</style>
</head>
<body>
  <section class="card card-front">
    <div class="brand">
      <span class="brand-dot"></span>
      <div class="brand-name">Tallow Partners</div>
    </div>
    <div class="contact">
      <div class="person-name"><span class="first">Dorian</span> <span class="last">Whitlock</span></div>
      <div class="role">Managing Director</div>
      <div class="line">
        <svg viewBox="0 0 14 12" aria-hidden="true"><path fill="#ec6723" d="M1 4c0-2 3-3 6-3s6 1 6 3v1.5h-3V4H4v1.5H1zM3 6h8l2 5H1z"/></svg>
        <span>(+244) 947 582 316</span>
      </div>
      <div class="line">
        <svg viewBox="0 0 14 12" aria-hidden="true"><rect x="1" y="2" width="12" height="9" fill="#ec6723"/><path d="M1 2l6 5 6-5" fill="none" stroke="#fff" stroke-width="1.2"/></svg>
        <span>dorian.whitlock@tallow-p.example</span>
      </div>
      <div class="address">
        N ° 17/18 Rua Veloso - R / C<br>
        2B Direita<br>
        Bairro Mutamba - Luanda
      </div>
    </div>
  </section>

  <section class="card card-back">
    <div class="back-mark">
      <span class="brand-dot"></span>
    </div>
  </section>
</body>
</html>
```